Business card for law firm

Need business card for new law firm. Think confident, authoritative, conservative, but not stuffy or old-fashioned.

Contact Information for Business Card

Content for card - logo (uploaded), plus the following:

Paul Whitcombe (larger font)
Managing Partner (larger font, but not as large as name)
Level 9, 7 Ferris Lane
Sydney NSW 2000
Main Tel 02 9364 2710
Direct Tel 02 8472 3159
Email paul@qvlegal.com.au
www.qvlegal.com.au

Letterhead design should include logo plus:
Level 9, 7 Ferris Lane
Sydney NSW 2000
Tel 02 8472 3159
www.qvlegal.com.au

```html
<!DOCTYPE html>
<html lang="en">
<head>
<meta charset="utf-8">
<title>Quayvale Legal – Business Card</title>
<link rel="stylesheet" href="https://fonts.googleapis.com/css2?family=Jost:wght@400;500;600;700&display=swap">
<style>
  :root {
    --backdrop: #3a3a3c;
    --navy: #0b1f5c;
    --navy-deep: #061649;
    --card-light: #ececec;
    --ink: #1d1d1f;
    --white: #ffffff;
    --rule: #2a2a2a;
  }
  * { margin: 0; padding: 0; box-sizing: border-box; }
  html, body {
    width: 1200px;
    height: 1000px;
    overflow: hidden;
    background: var(--backdrop);
    font-family: "Jost", Arial, sans-serif;
  }
  .canvas {
    position: relative;
    width: 1200px;
    height: 1000px;
  }
  .card {
    position: absolute;
    left: 270px;
    width: 660px;
    height: 403px;
    border-radius: 26px;
  }
  /* Back of card */
  .card--back {
    top: 64px;
    background: linear-gradient(160deg, var(--navy) 0%, var(--navy-deep) 100%);
    color: var(--white);
  }
  .card--back .wordmark {
    position: absolute;
    right: 70px;
    top: 130px;
    text-align: right;
    color: var(--white);
  }
  .wordmark__line {
    display: block;
    font-weight: 500;
    text-transform: uppercase;
    line-height: 1.05;
  }
  .wordmark__line--main { font-size: 56px; letter-spacing: 3px; }
  .wordmark__line--sub { font-size: 22px; letter-spacing: 14px; margin-top: 6px; }
  .wordmark__mark {
    display: inline-block;
    width: 60px;
    height: 60px;
    margin-bottom: 18px;
    background: currentColor;
  }
  .card--back .web {
    position: absolute;
    right: 110px;
    bottom: 52px;
    font-size: 18px;
    font-weight: 500;
    letter-spacing: 1px;
  }
  /* Front of card */
  .card--front {
    top: 533px;
    background: var(--card-light);
    color: var(--ink);
  }
  .card--front .wordmark {
    position: absolute;
    left: 40px;
    top: 120px;
    width: 280px;
    text-align: center;
    color: var(--navy);
  }
  .card--front .wordmark__line--main { font-size: 40px; letter-spacing: 2px; }
  .card--front .wordmark__line--sub { font-size: 17px; letter-spacing: 11px; }
  .card--front .wordmark__mark { width: 50px; height: 50px; margin-bottom: 14px; }
  .divider {
    position: absolute;
    left: 340px;
    top: 80px;
    width: 2px;
    height: 250px;
    background: var(--rule);
  }
  .divider__accent {
    position: absolute;
    left: 340px;
    top: 80px;
    width: 4px;
    height: 44px;
    background: var(--navy);
  }
  .contact {
    position: absolute;
    left: 362px;
    top: 80px;
    width: 280px;
    font-size: 15.5px;
    line-height: 1.35;
  }
  .contact__name {
    font-size: 24px;
    font-weight: 700;
    color: var(--navy);
    text-transform: uppercase;
    letter-spacing: 0.5px;
    line-height: 1.1;
  }
  .contact__role {
    font-size: 18px;
    margin-bottom: 14px;
  }
  .contact__address { margin-bottom: 12px; }
  .contact__label { font-weight: 700; color: var(--navy); }
  .contact__row { display: flex; align-items: center; gap: 7px; }
  .contact__row svg { width: 16px; height: 16px; flex: none; }
  .contact__web strong { font-weight: 700; color: var(--navy); }
</style>
</head>
<body>
<main class="canvas">

  <section class="card card--back" aria-label="Card back">
    <div class="wordmark">
      <span class="wordmark__mark" aria-hidden="true"></span>
      <span class="wordmark__line wordmark__line--main">Quayvale</span>
      <span class="wordmark__line wordmark__line--sub">Legal</span>
    </div>
    <p class="web">www.qvlegal.com.au</p>
  </section>

  <section class="card card--front" aria-label="Card front">
    <div class="wordmark">
      <span class="wordmark__mark" aria-hidden="true"></span>
      <span class="wordmark__line wordmark__line--main">Quayvale</span>
      <span class="wordmark__line wordmark__line--sub">Legal</span>
    </div>

    <span class="divider" aria-hidden="true"></span>
    <span class="divider__accent" aria-hidden="true"></span>

    <div class="contact">
      <p class="contact__name">Paul Whitcombe</p>
      <p class="contact__role">Managing Partner</p>
      <p class="contact__address">Level 9, 7 Ferris Lane<br>Sydney NSW 2000</p>
      <p><span class="contact__label">Main Tel</span> 02 9364 2710</p>
      <p><span class="contact__label">Direct Tel</span> 02 8472 3159</p>
      <p class="contact__row">
        <svg viewBox="0 0 16 16" aria-hidden="true"><rect x="1" y="3" width="14" height="10" rx="1" fill="#0b1f5c"/><path d="M1.5 3.5 L8 9 L14.5 3.5" stroke="#fff" stroke-width="1.3" fill="none"/></svg>
        paul@qvlegal.com.au
      </p>
      <p class="contact__row contact__web">
        <svg viewBox="0 0 16 16" aria-hidden="true"><circle cx="8" cy="8" r="7" fill="#0b1f5c"/><g stroke="#fff" stroke-width="0.9" fill="none"><ellipse cx="8" cy="8" rx="3" ry="7"/><path d="M1 8 H15 M2.2 4.5 H13.8 M2.2 11.5 H13.8"/></g></svg>
        <span>www.<strong>qvlegal.com</strong>.au</span>
      </p>
    </div>
  </section>

</main>
</body>
</html>
```